Business card for medical clinic

I need an upmarket, modern medical/health business card for my clinic

Contact Information for Business Card

name, address, email, qr code

```html
<!DOCTYPE html>
<html lang="en">
<head>
<meta charset="utf-8">
<title>Northbay Care Partners – Business Card</title>
<link rel="stylesheet" href="https://fonts.googleapis.com/css2?family=Poppins:wght@300;400;500;600;700&display=swap">
<style>
  :root {
    --backdrop: #222222;
    --paper: #ffffff;
    --ink: #111111;
    --brand-blue: #1ea3e0;
    --brand-navy: #1c3152;
    --gradient-top: #1b2846;
    --gradient-mid: #1a7fb4;
    --gradient-low: #23a9e3;
  }
  * { box-sizing: border-box; margin: 0; padding: 0; }
  html, body {
    width: 1200px; height: 780px; overflow: hidden;
    background: var(--backdrop);
    font-family: "Poppins", sans-serif;
  }
  .canvas {
    position: relative; width: 1200px; height: 780px;
    display: flex; align-items: center; justify-content: center; gap: 40px;
  }
  .card {
    width: 540px; height: 309px; position: relative; overflow: hidden;
    box-shadow: 0 14px 30px rgba(0,0,0,.55);
  }

  /* Front side */
  .card-front { background: var(--paper); border-bottom: 4px solid var(--brand-blue); display: flex; }
  .front-brand {
    width: 236px; display: flex; align-items: center; justify-content: center; gap: 10px;
  }
  .brand-dot {
    width: 22px; height: 22px; border-radius: 50%; background: var(--brand-navy); flex: none;
  }
  .brand-name {
    font-weight: 600; font-size: 17px; line-height: 1.15; letter-spacing: .06em;
    text-transform: uppercase; color: var(--brand-navy);
  }
  .front-divider { width: 1px; background: var(--brand-blue); margin: 62px 0; }
  .front-details { padding: 54px 0 0 30px; }
  .person-name { font-size: 29px; line-height: 1; color: var(--brand-blue); }
  .person-name .first { font-weight: 700; }
  .person-name .last { font-weight: 300; }
  .person-title { font-size: 13px; font-weight: 500; color: var(--ink); margin-top: 6px; }
  .address { font-size: 12.5px; color: var(--brand-blue); line-height: 1.5; margin-top: 16px; }
  .contacts { list-style: none; margin-top: 14px; }
  .contacts li {
    display: flex; align-items: center; gap: 9px;
    font-size: 12.5px; color: var(--ink); line-height: 1.75;
  }
  .contacts svg { width: 13px; height: 13px; flex: none; }

  /* Back side */
  .card-back {
    background: linear-gradient(205deg, var(--gradient-top) 0%, var(--gradient-mid) 45%, var(--gradient-low) 100%);
    display: flex; align-items: center; justify-content: center; gap: 16px;
  }
  .card-back .brand-dot { width: 34px; height: 34px; background: var(--paper); }
  .card-back .brand-name { color: var(--paper); font-size: 25px; }
</style>
</head>
<body>
<main class="canvas">
  <section class="card card-front" aria-label="Card front">
    <div class="front-brand">
      <span class="brand-dot"></span>
      <span class="brand-name">Northbay Care<br>Partners</span>
    </div>
    <div class="front-divider"></div>
    <div class="front-details">
      <h1 class="person-name"><span class="first">Marta</span> <span class="last">Velinova</span></h1>
      <p class="person-title">Founder &amp; CEO</p>
      <p class="address">1840 Cedar Hollow Rd. Suite 310<br>Millbrook, TX 75990</p>
      <ul class="contacts">
        <li>
          <svg viewBox="0 0 16 16" aria-hidden="true"><path fill="#1ea3e0" d="M3.6 1.5l2.2 2.6-1.3 1.6c.9 1.9 2.2 3.2 4.1 4.1l1.6-1.3 2.6 2.2-1.1 2.3C6.5 14.6 1.4 9.5 1.3 2.6z"/></svg>
          (555) 214-6093
        </li>
        <li>
          <svg viewBox="0 0 16 16" aria-hidden="true"><rect x="1" y="3" width="14" height="10" rx="1.5" fill="#1ea3e0"/><path d="M1.8 4l6.2 4.6L14.2 4" fill="none" stroke="#fff" stroke-width="1.2"/></svg>
          hello@northbaycare.com
        </li>
        <li>
          <svg viewBox="0 0 16 16" aria-hidden="true"><circle cx="8" cy="8" r="6.5" fill="none" stroke="#1ea3e0" stroke-width="1.4"/><ellipse cx="8" cy="8" rx="2.7" ry="6.5" fill="none" stroke="#1ea3e0" stroke-width="1.2"/><path d="M1.5 8h13" stroke="#1ea3e0" stroke-width="1.2"/></svg>
          www.northbaycare.com
        </li>
      </ul>
    </div>
  </section>

  <section class="card card-back" aria-label="Card back">
    <span class="brand-dot"></span>
    <span class="brand-name">Northbay Care<br>Partners</span>
  </section>
</main>
</body>
</html>
```